Business card for Crestline Bathrooms

Please design a business card for our bathroom renovation business. You can use my existing logo, but if you have an idea to modernize it, I would like to see it. Please see attached files first. I would like to use the blue and the orange theme. I like the concept of using the shower head in the logo. Please find following a design (or two) that I have been trying to create with my limited resources. That design was for a sign, but I was going to adopt it and use it as a business card as well. I like the concept of the water splash but I don’t think it “flows” nicely together with the logo. Another thought is that maybe creating the logo out of water splash could work and have a dramatic effect (like the water text and the butterfly picture attached with similar background instead of white). If the above doesn’t work I would like to see a modern simplified design. One of the attached files named as the unwanted business card has all the details that I want included in the business card. Please note that it is two sided.
Updates

I am very thankful for the designs that I have received, but they are very similar and only a couple of attempts to do something with the water splash as per my original brief. Modernizing the logo and having it made out of out of water splash with the orange as color accent could work and have a dramatic effect (like the water text and the butterfly picture attached with similar background instead of white). Please do not use the butterfly itself! This is just an example that images can be created out of water splash.

Contact Information for Business Card

all the details are on the unwonted business card file included

Colors
3176b5

Requirements
Nice to have
• Copied from the brief:
• ... maybe creating the logo out of water splash could work and have a dramatic effect (like the water text and the butterfly picture attached with similar background instead of white). Please do not use the butterfly itself!
Should not have
• I am getting designs with a butterfly. The butterfly picture was an example of creating something from a water splash. The butterfly itself has no association with anything other than the concept of creating a logo out of water splash. Sorry, I thought I was clear in the brief.

```html
<!DOCTYPE html>
<html lang="en">
<head>
<meta charset="utf-8">
<title>Crestline Bathrooms – Business Card</title>
<link href="https://fonts.googleapis.com/css2?family=Arimo:wght@400;700&display=swap" rel="stylesheet">
<style>
  :root{
    --backdrop:#2b2b2d;
    --card-dark:#0d0d0d;
    --card-light:#f7f7f7;
    --coral:#e8766c;
    --navy:#1e4f80;
    --ink:#3a3a3a;
    --rule:#5a5a5a;
    --white:#ffffff;
  }
  *{box-sizing:border-box;margin:0;padding:0}
  html,body{width:1200px;height:900px;overflow:hidden}
  body{
    background:var(--backdrop);
    font-family:"Arimo",Arial,sans-serif;
    position:relative;
  }
  .card{
    position:absolute;
    left:300px;
    width:600px;
    height:340px;
    overflow:hidden;
  }
  /* back side */
  .card-back{top:70px;background:var(--card-dark);color:var(--white)}
  .card-back .accent-band{position:absolute;left:0;right:0;bottom:0;height:9px;background:var(--coral)}
  .services{
    position:absolute;top:70px;left:0;right:0;
    text-align:center;list-style:none;
    font-size:15px;letter-spacing:.5px;line-height:22px;text-transform:uppercase;
  }
  .services-rule{
    position:absolute;top:172px;left:95px;right:95px;height:1px;background:var(--rule);
  }
  .memberships{
    position:absolute;top:196px;left:0;right:0;
    display:flex;justify-content:center;align-items:center;gap:34px;
  }
  .badge{background:var(--white)}
  .badge-round{width:66px;height:72px;border-radius:16px}
  .badge-block{width:180px;height:56px;border-radius:4px}

  /* front side */
  .card-front{top:480px;background:var(--card-light);color:var(--ink)}
  .card-front .accent-band{position:absolute;left:0;right:0;bottom:0;height:9px;background:var(--navy)}
  .brand{
    position:absolute;left:34px;top:120px;width:230px;
    display:flex;align-items:center;gap:12px;
  }
  .brand-dot{width:22px;height:22px;border-radius:50%;background:var(--coral);flex:none}
  .brand-name{
    font-size:28px;font-weight:700;color:var(--navy);line-height:32px;
  }
  .divider{position:absolute;left:285px;top:60px;width:1px;height:200px;background:#d4d4d4}
  .contact{position:absolute;left:310px;top:74px;right:20px}
  .contact-name{
    font-size:21px;font-weight:700;color:var(--coral);
    text-transform:uppercase;letter-spacing:.3px;margin-bottom:14px;
  }
  .contact-list{list-style:none;font-size:15px;line-height:22px}
  .contact-list li{display:flex;align-items:center;gap:8px}
  .contact-list svg{width:13px;height:13px;flex:none;fill:var(--coral)}
  .contact-address{font-size:15.5px;margin-top:8px}
</style>
</head>
<body>

<section class="card card-back" aria-label="Card back">
  <ul class="services">
    <li>Complete bathroom renovations &amp; remodelling</li>
    <li>Highly skilled &amp; qualified tradespeople</li>
    <li>Professional service from concept to completion</li>
    <li>All work guaranteed</li>
  </ul>
  <div class="services-rule"></div>
  <div class="memberships">
    <div class="badge badge-round" role="img" aria-label="Trade association membership badge"></div>
    <div class="badge badge-block" role="img" aria-label="Builders association membership badge"></div>
  </div>
  <div class="accent-band"></div>
</section>

<section class="card card-front" aria-label="Card front">
  <div class="brand">
    <span class="brand-dot"></span>
    <span class="brand-name">Crestline Bathrooms</span>
  </div>
  <div class="divider"></div>
  <div class="contact">
    <p class="contact-name">Daniel Morrow</p>
    <ul class="contact-list">
      <li><svg viewBox="0 0 16 16" aria-hidden="true"><path d="M3 1l3 3-1.5 2a9 9 0 0 0 5.5 5.5L12 10l3 3-2 2C6 15 1 10 1 3z"/></svg>0400 555 218</li>
      <li><svg viewBox="0 0 16 16" aria-hidden="true"><path d="M4 0h8a1 1 0 0 1 1 1v14a1 1 0 0 1-1 1H4a1 1 0 0 1-1-1V1a1 1 0 0 1 1-1zm1 2v10h6V2zm3 11a1 1 0 1 0 0 2 1 1 0 0 0 0-2z"/></svg>6200 5190</li>
      <li><svg viewBox="0 0 16 16" aria-hidden="true"><path d="M1 3h14v10H1zm1 1v.5l6 4 6-4V4z"/></svg>daniel@crestlinebathrooms.com.au</li>
      <li><svg viewBox="0 0 16 16" aria-hidden="true"><circle cx="8" cy="8" r="7"/></svg>crestlinebathrooms.com.au</li>
    </ul>
    <p class="contact-address">PO Box 41 Hollowbrook 2600</p>
  </div>
  <div class="accent-band"></div>
</section>

</body>
</html>
```